Creation of an elegant and modern turnkey Shopify website

Hello,

We are a new company specializing in the sale of above-ground pools. We want to create a turnkey website, ideally using Shopify. For now, we need a "showcase" site, not an e-commerce platform, with four tabs:

Home Page (an overall presentation of the company)
Our Products (an overview of all the above-ground pools we sell)
Our Projects (a page inspired by Snapgrid to showcase photos of our future projects)
Contact (a page with all our contact information and a contact form)

We are looking to create a highly visual, elegant, and modern website with vibrant splashes of color. We will provide the text, photos (along with instructions on where to place them on each page), and all other necessary information as attachments.

Thank you in advance for your proposals!

The Brisa Lagoon Team

Target Market(s)

Targeted at Swiss customers (a translator will need to be installed for different languages)

Industry/Entity Type

Sale of customised above-ground pools

Coding

Coded - Design and coding required

Font styles to use
Sans Serif

Colors
0094D4
00A9DD
6FCCEA
C7EBF8
E9F6FB
00AB8E
00BBA5
67D7C9
C6EFE9
E9F9F6

Requirements
Must have
• A stunning, elegant and modern look
Nice to have
• Inspiration from the colors of our logo throughout the site, but in an elegant way
Should not have
• An overly classic look for swimming pool sites

```html
<!DOCTYPE html>
<html lang="en">
<head>
<meta charset="utf-8">
<title>Brisa Lagoon – Landing Page Mobile View</title>
<link href="https://fonts.googleapis.com/css2?family=Open+Sans:wght@300;400;600;700&family=Poppins:wght@400;500;600&display=swap" rel="stylesheet">
<style>
  :root{
    --page-bg:#fcf8f6;
    --sky:#c7ebf8;
    --sky-soft:#e9f6fb;
    --cyan:#00a9dd;
    --cyan-bright:#00c8e6;
    --green:#00ab8e;
    --green-mid:#2fb39c;
    --teal-panel:#3aa99a;
    --aqua-panel:#95dde3;
    --navy:#2b3a67;
    --ink:#2a2a2a;
    --muted:#5f6b73;
    --white:#ffffff;
  }
  *{box-sizing:border-box;margin:0;padding:0}
  html,body{width:1200px;height:1200px;overflow:hidden}
  body{background:var(--page-bg);font-family:"Open Sans",sans-serif;color:var(--ink);position:relative}

  .intro{position:absolute;left:70px;top:130px;width:250px}
  .intro__brand{font-family:"Open Sans",sans-serif;font-weight:300;font-size:40px;line-height:1.05;color:var(--cyan-bright);letter-spacing:1px}
  .intro__title{margin-top:60px;font-family:"Poppins",sans-serif;font-weight:500;font-size:26px;line-height:1.3;color:var(--ink)}

  .column{position:absolute;top:40px;width:200px;display:flex;flex-direction:column;gap:14px}
  .col-1{left:345px}.col-2{left:560px}.col-3{left:775px}.col-4{left:990px}

  .card{border-radius:16px;overflow:hidden;box-shadow:0 10px 28px rgba(40,70,90,.12);background:var(--sky)}
  .photo{display:block;width:100%}

  /* hero */
  .topbar{height:34px;background:var(--white);display:flex;align-items:center;justify-content:space-between;padding:0 12px}
  .topbar__brand{font-size:10px;font-weight:400;color:var(--cyan)}
  .hero{padding:16px 14px 14px}
  .hero__title{font-weight:700;font-size:18px;line-height:1.28;color:var(--green)}
  .hero__text{margin-top:8px;font-size:8px;line-height:1.5;color:var(--muted)}
  .btn{display:inline-block;margin-top:10px;background:var(--green);color:var(--white);font-size:8px;font-weight:700;padding:8px 18px}
  .btn--wide{display:block;text-align:center}

  .section{padding:16px 14px}
  .eyebrow{font-size:8px;color:var(--muted);text-align:center}
  .heading{font-family:"Poppins",sans-serif;font-weight:500;font-size:16px;line-height:1.3;color:var(--navy);text-align:center;margin-top:4px}
  .heading--green{font-family:"Open Sans",sans-serif;font-weight:600;color:var(--green-mid)}
  .body{font-size:7.5px;line-height:1.6;color:var(--muted);text-align:center;margin-top:8px}

  .steps{display:flex;flex-direction:column;gap:10px;margin-top:12px}
  .step{background:var(--white);padding:14px 12px;text-align:center}
  .step__num{width:22px;height:22px;border-radius:50%;background:var(--green);color:var(--white);font-size:10px;font-weight:700;display:flex;align-items:center;justify-content:center;margin:0 auto 6px}
  .step__title{font-size:8.5px;font-weight:700;color:var(--navy)}
  .step__text{font-size:7px;line-height:1.5;color:var(--muted);margin-top:4px}

  /* about */
  .about{background:var(--teal-panel);color:var(--white);padding:16px 14px}
  .about .eyebrow{color:var(--white);text-align:left}
  .about__title{font-weight:600;font-size:16px;margin-top:6px}
  .about__text{font-size:7.5px;line-height:1.65;margin-top:8px}
  .outline-btn{display:inline-flex;align-items:center;gap:6px;margin-top:12px;font-size:8px;border:1px solid currentColor;padding:6px 14px}
  .about .outline-btn{border-radius:14px;border-style:dashed}
  .outline-btn--green{color:var(--green-mid)}

  /* gallery */
  .gallery{display:grid;grid-template-columns:1fr 1fr;grid-auto-rows:86px}
  .gallery__caption{background:var(--sky-soft);padding:12px 8px;font-size:7.5px;line-height:1.4}
  .gallery__caption strong{display:block;font-size:8px;color:var(--ink)}
  .gallery__caption span{color:var(--muted);font-size:7px}

  .cta{position:relative;height:250px;background:linear-gradient(160deg,#2f7a72,#1f5f5a 60%,#2c6e68)}
  .cta__inner{position:absolute;inset:0;padding:22px 14px;color:var(--white)}
  .cta__title{font-weight:700;font-size:14px;line-height:1.35}
  .cta__text{font-size:7px;margin-top:8px;opacity:.85}
  .cta .btn{position:absolute;left:14px;right:14px;bottom:16px;text-align:center;padding:10px}

  /* product */
  .product__body{padding:12px 14px;background:var(--sky-soft)}
  .product__title{font-size:11px;font-weight:600;color:var(--ink)}
  .product__meta{display:flex;gap:14px;margin-top:6px;font-size:7.5px;color:var(--muted)}
  .product__meta span{display:flex;align-items:center;gap:4px}

  /* footer */
  .footer{background:var(--aqua-panel);padding:18px 14px;color:var(--ink)}
  .footer__brand{font-size:16px;font-weight:300;color:var(--ink)}
  .footer__label{font-size:8px;font-weight:700;margin-top:10px}
  .newsletter{display:flex;margin-top:6px}
  .newsletter__input{flex:1;background:var(--white);font-size:7px;color:var(--muted);padding:7px 8px}
  .newsletter__send{background:var(--green);color:var(--white);font-size:7.5px;font-weight:700;padding:7px 10px}
  .footer__cols{display:grid;grid-template-columns:1fr 1fr;gap:10px;margin-top:14px}
  .footer__group h4{font-size:8.5px;font-weight:700;margin-bottom:5px}
  .footer__group li{list-style:none;font-size:7.5px;line-height:1.9;color:#2f4a4f}
</style>
</head>
<body>

<div class="intro">
  <div class="intro__brand">Brisa Lagoon</div>
  <h1 class="intro__title">Landing Page<br>Mobile view</h1>
</div>

<!-- column 1: hero and why us -->
<div class="column col-1">
  <div class="card">
    <div class="topbar">
      <span class="topbar__brand">Brisa Lagoon</span>
      <svg width="14" height="10" viewBox="0 0 14 10" aria-hidden="true"><path d="M0 1h14M0 5h14M4 9h10" stroke="#00ab8e" stroke-width="1.4"/></svg>
    </div>
    <div class="hero">
      <h2 class="hero__title">Transform Your Garden with Our Premium Above-Ground Pools!</h2>
      <p class="hero__text">Achieve your dreams with our custom, tailor-made above-ground pools.</p>
      <span class="btn">Get started</span>
    </div>
    <div class="photo" role="img" aria-label="Aerial view of a clear pool with a swimmer on a pink float" style="height:190px;background:linear-gradient(150deg,#bfe9ee,#8fd6dc 55%,#a9dfe2)"></div>
  </div>

  <div class="card section">
    <p class="eyebrow">Why Us</p>
    <h3 class="heading">Acquisition strategy and future plans</h3>
    <p class="body">Borem ipsum dolor sit amet, consectetur adipiscing elit. Etiam eu turpis molestie, dictum est a, mattis tellus. Sed dignissim, metus nec fringilla.</p>
    <div class="steps">
      <div class="step"><div class="step__num">1</div><p class="step__title">Superior Quality</p><p class="step__text">Each pool is constructed with high-quality materials, ensuring exceptional durability and strength.</p></div>
      <div class="step"><div class="step__num">2</div><p class="step__title">Elegant Design</p><p class="step__text">Our pools come in a variety of styles and finishes, seamlessly blending into any garden setting.</p></div>
      <div class="step"><div class="step__num">3</div><p class="step__title">Expert Support</p><p class="step__text">Our team guides you from the first sketch to installation and beyond.</p></div>
    </div>
  </div>
</div>

<!-- column 2: about and services -->
<div class="column col-2">
  <div class="card">
    <div class="about">
      <p class="eyebrow">About Us</p>
      <h3 class="about__title">About Brisa Lagoon</h3>
      <p class="about__text">Cedar Hollow Ranch is legendary for it's Native &amp; Exotic hunting which includes whitetail deer hunting, turkey hunting, and 60+ additional species available for hunt! You will see thousands of wildlife free ranging on over 18,000 acres of Alpine Valley. A few of the species you will encounter on your visit include giraffes, zebras, kangaroos, axis, bongo, kudu, blackbucks, elk, hogs, red stags, and of course record breaking whitetail deer. Cedar Hollow Ranch is home to tankride.example which is the only place in the world you can drive and shoot real WWII tanks.</p>
      <span class="outline-btn">Read more
        <svg width="8" height="8" viewBox="0 0 8 8" aria-hidden="true"><path d="M1 7L7 1M3 1h4v4" stroke="#fff" fill="none"/></svg></span>
    </div>
    <div class="photo" role="img" aria-label="Modern white villa under a blue sky" style="height:160px;background:linear-gradient(180deg,#6aa6e0,#b9d6ef 55%,#e7eef2)"></div>
  </div>

  <div class="card section">
    <p class="eyebrow">Our Services</p>
    <h3 class="heading heading--green">Personalized Services</h3>
    <p class="body">We understand that every garden and client is unique. That's why we offer personalized services, from design to installation and after-sales support. Our team of experts is here to answer all your questions and guide you throughout your project.</p>
    <div style="text-align:center"><span class="outline-btn outline-btn--green">Read more
      <svg width="8" height="8" viewBox="0 0 8 8" aria-hidden="true"><path d="M1 7L7 1M3 1h4v4" stroke="#2fb39c" fill="none"/></svg></span></div>
  </div>
</div>

<!-- column 3: satisfaction, gallery, contact -->
<div class="column col-3">
  <div class="card section">
    <p class="eyebrow">Our Services</p>
    <h3 class="heading heading--green">Guaranteed Satisfaction</h3>
    <p class="body">Your satisfaction is our top priority. We are committed to providing you with exceptional service and the highest quality products. Join our community of satisfied customers who are already enjoying their custom above-ground pools. 10-Year Warranty!</p>
    <div style="text-align:center"><span class="outline-btn outline-btn--green">Read more
      <svg width="8" height="8" viewBox="0 0 8 8" aria-hidden="true"><path d="M1 7L7 1M3 1h4v4" stroke="#2fb39c" fill="none"/></svg></span></div>
  </div>

  <div class="card">
    <div class="gallery">
      <div role="img" aria-label="Round pool at sunset" style="background:linear-gradient(140deg,#d49a5b,#3d6f8c)"></div>
      <div class="gallery__caption"><strong>Brisa Lagoon</strong>Project Gallery 1<br><span>Borem ipsum dolor sit amet</span></div>
      <div role="img" aria-label="Aerial view of pools among trees" style="background:linear-gradient(140deg,#3e7f3a,#2ea8d8)"></div>
      <div class="gallery__caption"><strong>Brisa Lagoon</strong>Project Gallery 2<br><span>Borem ipsum dolor sit amet</span></div>
      <div role="img" aria-label="Indoor pool hall" style="background:linear-gradient(140deg,#8fc3dd,#2f7fb2)"></div>
      <div class="gallery__caption"><strong>Brisa Lagoon</strong>Project Gallery 3<br><span>Borem ipsum dolor sit amet</span></div>
    </div>
    <div class="cta">
      <div class="cta__inner" role="img" aria-label="Swimmer in deep green water behind the call to action">
        <h3 class="cta__title">Contact Us Today To Discover Our Range Of Customizable Above-Ground Pools And Get A Tailored Quote</h3>
        <p class="cta__text">Lorem ipsum dolor sit amet, consectetur adipiscing. Et nunc vulputate libero.</p>
      </div>
      <span class="btn">Contact Us</span>
    </div>
  </div>
</div>

<!-- column 4: product and footer -->
<div class="column col-4">
  <div class="card">
    <div class="photo" role="img" aria-label="Blue lap pool with lane lines" style="height:140px;background:linear-gradient(160deg,#1f6fb8,#3a9be0 60%,#d9e9f2)"></div>
    <div class="product__body">
      <p class="product__title">Indoor swimming pool</p>
      <div class="product__meta">
        <span><svg width="9" height="8" viewBox="0 0 9 8" aria-hidden="true"><path d="M1 7V1M1 4h7v3M1 4V3h3v1" stroke="#00ab8e" fill="none"/></svg>5 Rooms</span>
        <span><svg width="9" height="8" viewBox="0 0 9 8" aria-hidden="true"><path d="M1 7V1M1 4h7v3M1 4V3h3v1" stroke="#00ab8e" fill="none"/></svg>5 Rooms</span>
      </div>
      <span class="btn btn--wide">Detail</span>
    </div>
    <div class="photo" role="img" aria-label="Stone house on a green hillside" style="height:140px;background:linear-gradient(180deg,#aebfcc,#7d8f7a 60%,#3f5b3a)"></div>
  </div>

  <div class="card footer">
    <p class="footer__brand">Brisa Lagoon</p>
    <p class="footer__label">Get Our Weekly Newsletter (Zero Spam)</p>
    <div class="newsletter"><span class="newsletter__input">Type In Your Email</span><span class="newsletter__send">Send</span></div>
    <div class="footer__cols">
      <div class="footer__group"><h4>Navigation</h4><ul><li>Home</li><li>Features</li><li>Market</li><li>Blog</li><li>Career</li><li>About Us</li></ul></div>
      <div class="footer__group"><h4>Features</h4><ul><li>Crypto Wallet</li><li>Exchange Services</li><li>Investment Portfolio</li><li>Portfolio Management</li></ul></div>
      <div class="footer__group"><h4>Legal</h4><ul><li>Term Of Services</li><li>Privacy Policy</li><li>Licensed &amp; Regulation</li></ul></div>
      <div class="footer__group"><h4>Socials</h4><ul><li>Linkup</li><li>Chirper</li><li>Facepage</li><li>Snapgrid</li></ul></div>
    </div>
  </div>
</div>

</body>
</html>
```